Audio/ Video Packaging Design for a Technology company.

We need a packaging design for a bag that is 7" wide and 10" high. The design will be for a new line of audio/video products. We would like to see designs that represent a superior quality product that provides a pure connection. We want the equivalent of a nice retail bag that you would find in a store like Tallow Mart. It should be a maximum of three colors. We really want something sharp, professional and eye catching, not whimsical or cartoonish. I've included a couple of examples below. I don't really like the designs of the bags, but I want you to see examples of what I'm looking for.

The company logo, which is uploaded, should be on the design. The words "audio and video products" should be either underneath the logo or to the side. Also, somewhere on the bag, we would like the words "For a Pure Connection"

The winner of this contest will likely get the opportunity for additional work as we have more products ready to launch.

Target Market(s)

resellers, consumers - men 25-60

Industry/Entity Type

It Company

Requirements
Must have
• It should be a maximum of three colors. We really want something sharp, professional and eye catching, not whimsical or cartoonish
Nice to have
• Eye-catching design. Utilize the entire bag but don't make it too busy.
Should not have
• Whimsical, cartoonish

```html
<!DOCTYPE html>
<html lang="en">
<head>
<meta charset="utf-8">
<title>Veratone Audio and Video Products – Bag Packaging</title>
<link rel="stylesheet" href="https://fonts.googleapis.com/css2?family=Montserrat:wght@500&family=Exo+2:wght@300&family=PT+Sans+Narrow:wght@700&display=swap">
<style>
  :root {
    --stage: #6f97b6;
    --bag-blue: #1b78bf;
    --bag-blue-dark: #14569b;
    --bag-blue-light: #2aa0dc;
    --panel-white: #ffffff;
    --ink-navy: #1d3467;
    --pattern-light: #b9d6ef;
    --pattern-mid: #5d8fcf;
    --text-white: #ffffff;
  }
  html, body {
    margin: 0;
    padding: 0;
    width: 1200px;
    height: 787px;
    overflow: hidden;
    background: var(--stage);
  }
  .canvas {
    position: relative;
    width: 1200px;
    height: 787px;
  }
  .canvas svg { display: block; }
  .brand-name {
    font-family: "Montserrat", sans-serif;
    font-weight: 500;
    letter-spacing: 1px;
  }
  .product-line {
    font-family: "Exo 2", sans-serif;
    font-weight: 300;
  }
  .tagline, .origin-note {
    font-family: "PT Sans Narrow", sans-serif;
    font-weight: 700;
  }
</style>
</head>
<body>
<main class="canvas">
  <svg width="1200" height="787" viewBox="0 0 1200 787" aria-labelledby="bag-title">
    <title id="bag-title">Veratone bag packaging, front and back</title>
    <defs>
      <linearGradient id="bag-frame" x1="0" y1="0" x2="1" y2="1">
        <stop offset="0" stop-color="var(--bag-blue-light)"/>
        <stop offset="1" stop-color="var(--bag-blue-dark)"/>
      </linearGradient>
      <linearGradient id="back-panel" x1="0" y1="0" x2="1" y2="1">
        <stop offset="0" stop-color="#1c8bcc"/>
        <stop offset="0.6" stop-color="#1a6fb3"/>
        <stop offset="1" stop-color="#164f92"/>
      </linearGradient>
      <linearGradient id="front-pattern" x1="0" y1="0" x2="1" y2="1">
        <stop offset="0" stop-color="var(--pattern-mid)" stop-opacity="0.85"/>
        <stop offset="0.5" stop-color="var(--pattern-light)" stop-opacity="0.9"/>
        <stop offset="1" stop-color="var(--pattern-light)" stop-opacity="0"/>
      </linearGradient>
      <linearGradient id="back-pattern" x1="0" y1="0" x2="1" y2="0">
        <stop offset="0" stop-color="#0f4a8a" stop-opacity="0.45"/>
        <stop offset="1" stop-color="#0f4a8a" stop-opacity="0.1"/>
      </linearGradient>
      <linearGradient id="mark-disc" x1="0" y1="0" x2="0" y2="1">
        <stop offset="0" stop-color="#ffffff"/>
        <stop offset="1" stop-color="#e3e8ee"/>
      </linearGradient>
    </defs>

    <!-- Front of bag -->
    <g class="bag bag--front">
      <rect class="bag-frame" x="152" y="118" width="430" height="612" rx="22" fill="url(#bag-frame)"/>
      <rect class="bag-window" x="173" y="138" width="388" height="543" rx="16" fill="var(--panel-white)"/>
      <rect class="bag-window-foot" x="173" y="660" width="388" height="21" fill="var(--panel-white)"/>
      <g class="zip-seal" stroke="#e6ebf0" stroke-width="2">
        <line x1="173" y1="206" x2="561" y2="206"/>
        <line x1="173" y1="212" x2="561" y2="212"/>
        <line x1="173" y1="218" x2="561" y2="218"/>
      </g>
      <path class="pattern-area" role="img" aria-label="Abstract cascade of translucent blue rounded squares and light streaks"
            d="M173 232 H480 C430 300 360 360 330 430 C300 500 320 600 340 681 H173 Z" fill="url(#front-pattern)"/>
      <path class="hang-tab" d="M244 118 H490 V212 Q490 230 472 230 H262 Q244 230 244 212 Z" fill="url(#bag-frame)"/>
      <rect class="hang-hole" x="316" y="152" width="102" height="20" rx="10" fill="var(--panel-white)"/>
      <circle class="hang-hole-notch" cx="367" cy="150" r="7" fill="var(--panel-white)"/>

      <circle class="brand-disc" cx="424" cy="436" r="36" fill="url(#mark-disc)" stroke="#d3d9e0" stroke-width="2"/>
      <text class="brand-name" x="424" y="525" text-anchor="middle" font-size="38" fill="var(--ink-navy)">VERATONE</text>
      <text class="product-line" x="426" y="553" text-anchor="middle" font-size="19" fill="var(--ink-navy)">Audio and Video Products</text>

      <text class="tagline" x="367" y="715" text-anchor="middle" font-size="28" fill="var(--text-white)">For a Pure Connection</text>
    </g>

    <!-- Back of bag -->
    <g class="bag bag--back">
      <rect class="bag-frame" x="618" y="118" width="430" height="612" rx="22" fill="url(#bag-frame)"/>
      <rect class="bag-window" x="638" y="138" width="388" height="572" rx="16" fill="url(#back-panel)"/>
      <g class="zip-seal" stroke="#1a5f9f" stroke-width="2">
        <line x1="638" y1="206" x2="1026" y2="206"/>
        <line x1="638" y1="212" x2="1026" y2="212"/>
        <line x1="638" y1="218" x2="1026" y2="218"/>
      </g>
      <path class="pattern-area" role="img" aria-label="Faint band of outlined rounded squares sweeping across the top"
            d="M638 245 C720 250 820 280 1020 380 V410 C820 330 720 300 638 310 Z" fill="url(#back-pattern)"/>
      <path class="pattern-area" role="img" aria-label="Faint cluster of outlined rounded squares near the bottom"
            d="M638 600 C720 560 840 530 1020 520 V600 C860 610 740 640 638 660 Z" fill="url(#back-pattern)"/>
      <path class="hang-tab" d="M710 118 H955 V212 Q955 230 937 230 H728 Q710 230 710 212 Z" fill="url(#bag-frame)"/>
      <rect class="hang-hole" x="781" y="152" width="102" height="20" rx="10" fill="var(--panel-white)"/>
      <circle class="hang-hole-notch" cx="832" cy="150" r="7" fill="var(--panel-white)"/>

      <circle class="brand-disc" cx="830" cy="290" r="42" fill="url(#mark-disc)" stroke="#c9d2dc" stroke-width="2"/>
      <text class="brand-name" x="832" y="393" text-anchor="middle" font-size="40" fill="var(--text-white)">VERATONE</text>
      <text class="product-line" x="832" y="424" text-anchor="middle" font-size="20" fill="var(--text-white)">Audio and Video Products</text>

      <text class="origin-note" x="944" y="650" text-anchor="middle" font-size="13" fill="var(--text-white)">MADE IN CHINA</text>
      <g class="compliance-badges" fill="var(--panel-white)" stroke="#c9d2dc" stroke-width="2">
        <circle cx="896" cy="677" r="14"/>
        <circle cx="944" cy="677" r="14"/>
        <circle cx="992" cy="677" r="14"/>
      </g>
    </g>
  </svg>
</main>
</body>
</html>
```